Vape Brand Cartoon Packaging Design

I AM NOT PICKY!! Just need to get the basic job done and I will be happy. To start we need a text logo for our brand "Poma Frost" vape cartridges that is colorful, with a cartoonish design. We have 3 flavors we are starting with that need there own custom logo: Lagoon Drizzle (colorful pink packaging with ice cream sherbert incorporated in the cartoon design), Harbor Fudge (blue background with a white cake cartoon design), and Rocket Waffles (orange packaging with cartoon animated zimbo cookies acting crazy/fighting on it). I dont care if the images are sourced from google images or wherever. See the uploaded files for guidance I want them extremely similar to that packaging. The packaging is roughly 1.5 inches wide and 2.5 inches tall.
Where the packaging says "high ridge rarities" I want my brand name "Poma Frost", underneath it I want it to say "vape cartridge" just like in the picture. I also want the flavors in the same area on the package and for them all to say HYBRID and 1.0 gram in the same spot. Instead of 1.0 gram though have it say 1000 mg. To reiterate I want the packaging very similar to the packaging in the picture. There will be other flavors added in the near future so ideally I want someone I can work with in the long term!
Poma Frost

```html
<!DOCTYPE html>
<html lang="en">
<head>
<meta charset="utf-8">
<title>Poma Frost – Vape Cartridge Packaging</title>
<link rel="stylesheet" href="https://fonts.googleapis.com/css2?family=Roboto+Condensed:wght@700&family=Luckiest+Guy&display=swap">
<style>
  :root {
    --page-bg: #fde9c8;
    --page-bg-soft: #fff3dd;
    --brand-orange: #f28c1e;
    --label-orange: #f05a28;
    --outline-plum: #3a1030;

    --pink-edge: #ef6fae;
    --pink-core: #fde3ef;
    --pink-ink: #e6007e;
    --pink-logo: #d9468f;

    --blue-edge: #1fa6e2;
    --blue-core: #eef8fd;
    --blue-ink: #3a4f9e;
    --blue-logo: #2f8fbf;

    --orange-edge: #f4901f;
    --orange-core: #fff1dc;
    --orange-ink: #ee5a24;
    --orange-logo: #e97c14;
  }
  * { box-sizing: border-box; margin: 0; padding: 0; }
  html, body { width: 1200px; height: 1000px; overflow: hidden; }
  body {
    position: relative;
    background: radial-gradient(ellipse at center, var(--page-bg-soft), var(--page-bg));
    font-family: "Roboto Condensed", Arial, sans-serif;
  }

  .brand-header {
    position: absolute; top: 38px; left: 0; width: 1200px;
    text-align: center;
  }
  .brand-name {
    font-size: 138px; line-height: 160px; font-weight: 700;
    color: var(--brand-orange); letter-spacing: 2px;
    text-transform: uppercase;
  }
  .brand-tagline {
    margin-top: 10px;
    font-size: 34px; font-weight: 700; color: var(--label-orange);
    letter-spacing: 0.5px;
  }

  .package {
    position: absolute; top: 328px; width: 362px; height: 525px;
    text-align: center;
  }
  .package--lagoon { left: 39px;  background: radial-gradient(ellipse 60% 50% at 50% 52%, var(--pink-core), var(--pink-edge)); --ink: var(--pink-ink); --logo: var(--pink-logo); }
  .package--harbor { left: 427px; background: radial-gradient(ellipse 60% 50% at 50% 52%, var(--blue-core), var(--blue-edge)); --ink: var(--blue-ink); --logo: var(--blue-logo); }
  .package--rocket { left: 818px; background: radial-gradient(ellipse 60% 50% at 50% 52%, var(--orange-core), var(--orange-edge)); --ink: var(--orange-ink); --logo: var(--orange-logo); }

  .flavor-name {
    position: absolute; top: 24px; left: 0; width: 100%;
    font-family: "Luckiest Guy", "Arial Black", sans-serif;
    font-size: 31px; line-height: 34px; letter-spacing: 2px;
    color: #fff; -webkit-text-stroke: 1.5px var(--outline-plum);
    text-shadow: 2px 2px 0 var(--outline-plum);
    text-transform: uppercase;
  }
  .package-brand {
    position: absolute; top: 118px; left: 0; width: 100%;
    font-size: 56px; line-height: 72px; font-weight: 700;
    color: var(--logo); text-transform: uppercase; letter-spacing: 1px;
  }
  .package-tagline {
    position: absolute; top: 199px; left: 0; width: 100%;
    font-size: 14px; font-weight: 700; color: var(--ink);
  }
  .package-art {
    position: absolute; top: 228px; left: 86px; width: 190px; height: 205px;
    border-radius: 24px;
  }
  .package--lagoon .package-art { background: linear-gradient(160deg, #7fd6d8, #f6a4b4 45%, #8a4a36 80%, #e05aa0); }
  .package--harbor .package-art { left: 111px; width: 140px; background: linear-gradient(180deg, #f3dfc6, #ffffff 40%, #efe2d4 80%, #8a5a3a); }
  .package--rocket .package-art { left: 56px; width: 250px; background: linear-gradient(160deg, #d9a777, #8a5233 55%, #3a2418); border-radius: 40px; }

  .strain {
    position: absolute; top: 458px; left: 0; width: 100%;
    font-size: 20px; font-weight: 700; color: var(--ink);
  }
  .potency {
    position: absolute; top: 481px; left: 0; width: 100%;
    font-size: 14px; font-weight: 700; color: var(--ink);
  }
</style>
</head>
<body>
  <header class="brand-header">
    <h1 class="brand-name">Poma Frost</h1>
    <p class="brand-tagline">VAPE CARTRIDGE</p>
  </header>

  <section class="package package--lagoon">
    <h2 class="flavor-name">Lagoon<br>Drizzle</h2>
    <p class="package-brand">Poma Frost</p>
    <p class="package-tagline">VAPE CARTRIDGE</p>
    <div class="package-art" role="img" aria-label="Cartoon scoops of colorful sherbet ice cream stacked on a pink dessert stand"></div>
    <p class="strain">HYBRID</p>
    <p class="potency">1000 MG</p>
  </section>

  <section class="package package--harbor">
    <h2 class="flavor-name">Harbor<br>Fudge</h2>
    <p class="package-brand">Poma Frost</p>
    <p class="package-tagline">VAPE CARTRIDGE</p>
    <div class="package-art" role="img" aria-label="Cartoon three-tier white cake with brown heart decorations"></div>
    <p class="strain">HYBRID</p>
    <p class="potency">1000 MG</p>
  </section>

  <section class="package package--rocket">
    <h2 class="flavor-name">Rocket<br>Waffles</h2>
    <p class="package-brand">Poma Frost</p>
    <p class="package-tagline">VAPE CARTRIDGE</p>
    <div class="package-art" role="img" aria-label="Cartoon cup of cocoa with zimbo cookies jumping and scuffling around it"></div>
    <p class="strain">HYBRID</p>
    <p class="potency">1000 MG</p>
  </section>
</body>
</html>
```